Income Tax Flyer - Updates Needed

Just need to update this flyer design and give it a new look. We would like to keep all the same wording but make it stand out a little more. Our selling point is the "Same Day Tax Advance up to $6,000"

Lending, Small Loans, Tax Services, Title Loans, Personal Loans

```html
<!DOCTYPE html>
<html lang="en">
<head>
<meta charset="utf-8">
<title>Same Day Tax Advance Flyer</title>
<link rel="stylesheet" href="https://fonts.googleapis.com/css2?family=EB+Garamond:wght@400;600;700;800&display=swap">
<style>
  :root {
    --brand-green: #0a4a27;
    --deep-green: #07361c;
    --accent-red: #b5102a;
    --gold: #f2c14e;
    --ink: #111111;
    --paper: #ffffff;
    --photo-warm: #8a6248;
    --photo-cool: #b9bcbd;
  }
  html, body {
    margin: 0;
    padding: 0;
    overflow: hidden;
    background: var(--paper);
  }
  .flyer {
    position: relative;
    width: 927px;
    height: 1200px;
    overflow: hidden;
    background: var(--paper);
    font-family: "EB Garamond", Georgia, serif;
    color: var(--ink);
  }
  .hero-shapes {
    position: absolute;
    left: 0;
    top: 0;
    width: 927px;
    height: 470px;
  }
  .brand-name {
    position: absolute;
    left: 53px;
    top: 66px;
    margin: 0;
    color: var(--paper);
    font-weight: 600;
    font-size: 34px;
    line-height: 1;
    letter-spacing: 0.5px;
  }
  .brand-name span {
    display: block;
    font-size: 13px;
    letter-spacing: 3.5px;
    margin-top: 8px;
    margin-left: 66px;
  }
  .hero-headline {
    position: absolute;
    left: 53px;
    top: 165px;
    margin: 0;
    color: var(--paper);
    font-weight: 700;
    font-size: 45px;
    line-height: 68px;
  }

  /* Selling point band */
  .selling-band {
    position: absolute;
    left: 0;
    top: 482px;
    width: 927px;
    height: 168px;
    background: linear-gradient(180deg, var(--brand-green), var(--deep-green));
    border-top: 6px solid var(--accent-red);
    border-bottom: 6px solid var(--accent-red);
    box-sizing: border-box;
    text-align: center;
  }
  .selling-point { margin: 0; }
  .same-day-tag {
    display: inline-block;
    margin-top: 16px;
    padding: 4px 26px 2px;
    background: var(--accent-red);
    color: var(--paper);
    border-radius: 22px;
    font-weight: 800;
    font-size: 28px;
    line-height: 34px;
    letter-spacing: 4px;
  }
  .advance-line {
    display: block;
    margin-top: 10px;
    color: var(--paper);
    font-weight: 800;
    font-size: 50px;
    line-height: 70px;
    letter-spacing: 0.5px;
    white-space: nowrap;
  }
  .advance-amount {
    color: var(--gold);
    font-size: 62px;
  }

  .invite {
    position: absolute;
    left: 0;
    width: 927px;
    top: 676px;
    margin: 0;
    text-align: center;
    font-weight: 400;
    font-size: 52px;
    line-height: 1;
  }
  .invite-emphasis {
    position: absolute;
    left: 0;
    width: 927px;
    top: 738px;
    margin: 0;
    text-align: center;
    color: var(--accent-red);
    font-weight: 700;
    font-size: 76px;
    line-height: 1;
    letter-spacing: -0.5px;
  }
  .features {
    position: absolute;
    left: 0;
    top: 852px;
    width: 927px;
    height: 180px;
    margin: 0;
    padding: 0;
    list-style: none;
  }
  .feature {
    position: absolute;
    top: 0;
    width: 220px;
    margin-left: -110px;
    text-align: center;
  }
  .feature:nth-child(1) { left: 171px; }
  .feature:nth-child(2) { left: 462px; }
  .feature:nth-child(3) { left: 753px; }
  .feature svg { display: block; margin: 0 auto; }
  .feature-label {
    margin: 12px 0 0;
    font-weight: 700;
    font-size: 18px;
    line-height: 27px;
  }
  .contact {
    position: absolute;
    left: 62px;
    top: 1118px;
  }
  .contact-title {
    margin: 0;
    font-weight: 700;
    font-size: 27px;
    line-height: 30px;
  }
  .contact-phone {
    margin: 0;
    font-size: 21px;
    line-height: 30px;
  }
  .address-bar {
    position: absolute;
    left: 339px;
    top: 1116px;
    width: 588px;
    height: 70px;
    background: var(--brand-green);
    border-radius: 18px 0 0 18px;
    color: var(--paper);
    font-size: 22px;
    font-style: normal;
  }
  .address-bar .address-line {
    position: absolute;
    top: 20px;
    white-space: nowrap;
  }
  .address-bar .address-line:nth-child(1) { left: 34px; }
  .address-bar .address-line:nth-child(2) { left: 207px; }
  .address-bar .address-line:nth-child(3) { left: 385px; }
  .form-code {
    position: absolute;
    right: 6px;
    bottom: 5px;
    font-size: 8px;
    font-weight: 700;
    color: var(--paper);
  }
</style>
</head>
<body>
<main class="flyer">
  <svg class="hero-shapes" viewBox="0 0 927 470">
    <defs>
      <linearGradient id="photo-tone" x1="0" y1="0" x2="1" y2="1">
        <stop offset="0" stop-color="var(--photo-cool)" />
        <stop offset="0.55" stop-color="#9a8677" />
        <stop offset="1" stop-color="var(--photo-warm)" />
      </linearGradient>
    </defs>
    <polygon class="hero-panel" points="0,0 540,0 540,312 160,456 0,396" fill="var(--brand-green)" />
    <circle class="hero-photo" cx="760" cy="104" r="352" fill="url(#photo-tone)" stroke="var(--paper)" stroke-width="8"
            role="img" aria-label="Photo of a woman at a wooden office desk using a calculator beside a computer showing an invoice" />
  </svg>

  <p class="brand-name">Ledgerline<span>FINANCIAL GROUP</span></p>

  <h1 class="hero-headline">Apply Here For<br>$5,000 - $6,000<br>Today!</h1>

  <section class="selling-band">
    <h2 class="selling-point">
      <span class="same-day-tag">SAME DAY</span>
      <span class="advance-line">TAX ADVANCE UP TO <span class="advance-amount">$6,000</span></span>
    </h2>
  </section>

  <p class="invite">File Your Taxes&nbsp; And Apply For An</p>
  <p class="invite-emphasis">Easy Advance!</p>

  <ul class="features">
    <li class="feature">
      <svg width="200" height="110" viewBox="0 0 200 110" aria-hidden="true">
        <circle cx="100" cy="39" r="38" fill="var(--brand-green)" />
        <g fill="none" stroke="#fff" stroke-width="2" stroke-linecap="round">
          <path d="M120 26 A24 24 0 1 1 110 17" />
          <path d="M110 13 L111 18 L106 20" />
          <circle cx="100" cy="39" r="17" />
          <path d="M100 29 V39 L108 33" />
        </g>
        <path class="feature-arc" d="M9 106 Q100 40 191 106 Q100 62 9 106 Z" fill="var(--accent-red)" />
      </svg>
      <p class="feature-label">Available In<br>24 Hours or Less</p>
    </li>
    <li class="feature">
      <svg width="200" height="110" viewBox="0 0 200 110" aria-hidden="true">
        <circle cx="100" cy="39" r="38" fill="var(--brand-green)" />
        <g fill="none" stroke="#fff" stroke-width="2" stroke-linecap="round" stroke-linejoin="round">
          <circle cx="92" cy="50" r="13" />
          <path d="M86 36 L83 29 H101 L98 36" />
          <path d="M95 44 H90 A3 3 0 0 0 90 50 H94 A3 3 0 0 1 94 56 H89 M92 42 V58" />
          <circle cx="113" cy="28" r="11" />
          <path d="M108 28 L112 32 L119 24" />
        </g>
        <path class="feature-arc" d="M9 106 Q100 40 191 106 Q100 62 9 106 Z" fill="var(--accent-red)" />
      </svg>
      <p class="feature-label">Choose Your<br>Loan Amount</p>
    </li>
    <li class="feature">
      <svg width="200" height="110" viewBox="0 0 200 110" aria-hidden="true">
        <circle cx="100" cy="39" r="38" fill="var(--brand-green)" />
        <g fill="none" stroke="#fff" stroke-width="2" stroke-linecap="round" stroke-linejoin="round">
          <circle cx="90" cy="25" r="7" />
          <path d="M90 16 V18 M90 21 V25 L93 27" />
          <rect x="94" y="33" width="28" height="16" rx="2" transform="rotate(-35 108 41)" />
          <circle cx="108" cy="41" r="4" />
          <path d="M76 38 H88 M79 44 H91 M76 50 H88" />
        </g>
        <path class="feature-arc" d="M9 106 Q100 40 191 106 Q100 62 9 106 Z" fill="var(--accent-red)" />
      </svg>
      <p class="feature-label">Quick and Easy</p>
    </li>
  </ul>

  <section class="contact">
    <p class="contact-title">Contact Us Today!</p>
    <p class="contact-phone">Phone Number</p>
  </section>

  <address class="address-bar">
    <span class="address-line">Address line 1</span>
    <span class="address-line">Address line 2</span>
    <span class="address-line">Address line 3</span>
    <span class="form-code">C 25</span>
  </address>
</main>
</body>
</html>
```